Front and content page design for Fitness Cookbook

I am looking for someone to Design a front cover for a Recipe book and also create an amazing layout for the book.

Its for a corporate seminar so has to be eye catching, professional and bold.

Content is complete

Target Market(s)

Industry/Entity Type

Health And Wellness

Font styles to use
Sans Serif

Requirements
Must have
• Eye catching, professional and bold.
• By Dorian as stated on the document
• Must have Tidewell Motion Logo on it.

```html
<!DOCTYPE html>
<html lang="en">
<head>
<meta charset="utf-8">
<title>Peanut Butter Protein Cups</title>
<link href="https://fonts.googleapis.com/css2?family=Lato:wght@400;700&display=swap" rel="stylesheet">
<style>
  :root {
    --orange: #f39c1f;
    --ink: #2b2b2b;
    --paper: #ffffff;
    --photo-light: #e9e7e6;
    --photo-dark: #8f8a88;
  }
  html, body {
    margin: 0;
    padding: 0;
    overflow: hidden;
    background: var(--paper);
  }
  .page {
    position: relative;
    width: 849px;
    height: 1200px;
    overflow: hidden;
    background: var(--paper);
    font-family: "Lato", sans-serif;
    color: var(--ink);
  }
  .hero-photo {
    position: absolute;
    left: 0; top: 0;
    width: 849px; height: 518px;
    background: radial-gradient(ellipse at 48% 40%, #a07a5a 0%, #6e4a32 14%, var(--photo-light) 32%, #d9d6d4 60%, var(--photo-dark) 100%);
  }
  .title-band {
    position: absolute;
    left: 0; top: 518px;
    width: 849px; height: 150px;
    background: var(--orange);
    display: flex;
    align-items: center;
    justify-content: center;
  }
  .recipe-title {
    margin: 0;
    color: var(--paper);
    font-weight: 400;
    font-size: 50px;
    letter-spacing: 0.3px;
  }
  .recipe-body {
    position: absolute;
    left: 57px; top: 688px;
    width: 740px;
    font-size: 15px;
    line-height: 21px;
  }
  .label {
    color: var(--orange);
    font-weight: 700;
    font-size: 16px;
    text-transform: uppercase;
  }
  .meta { margin: 0; }
  .section-heading {
    margin: 22px 0 0;
    color: var(--orange);
    font-weight: 700;
    font-size: 16px;
    text-transform: uppercase;
  }
  .ingredients {
    list-style: none;
    margin: 0;
    padding: 0;
  }
  .instructions {
    margin: 0;
    line-height: 21px;
  }
  .ingredients + .section-heading { margin-top: 80px; }
  .page-footer {
    position: absolute;
    left: 57px; top: 1158px;
    display: flex;
    align-items: center;
    gap: 10px;
    font-size: 14px;
  }
  .brand {
    display: flex;
    align-items: center;
    gap: 5px;
    font-weight: 700;
    font-size: 12px;
    color: var(--ink);
  }
  .brand-dot {
    width: 10px; height: 10px;
    border-radius: 50%;
    background: var(--orange);
  }
</style>
</head>
<body>
<main class="page">
  <div class="hero-photo" role="img" aria-label="Photo of a stack of chocolate peanut butter protein cups on a white plate"></div>

  <header class="title-band">
    <h1 class="recipe-title">Peanut Butter Protein Cups</h1>
  </header>

  <section class="recipe-body">
    <p class="meta"><span class="label">Prep time</span> 30 mins</p>
    <p class="meta"><span class="label">Cooking time</span> 3 hours (freezer)</p>

    <h2 class="section-heading">Ingredients</h2>
    <ul class="ingredients">
      <li>1/3 cup coconut oil</li>
      <li>3 tablespoons cocoa powder</li>
      <li>3 tablespoons chocolate protein powder</li>
      <li>3 tablespoons 100% natural peanut butter</li>
    </ul>

    <h2 class="section-heading">Cooking instructions</h2>
    <p class="instructions">Grease a muffin tray with butter. Melt HALF the coconut oil in the microwave to a liquid and mix in HALF the protein powder and HALF the cocoa powder. Take the mixture and split evenly between the muffin tins (2-3 mm in each). Put tray into the freezer for 20 minutes.<br>
    Remove tray from freezer and evenly spoon peanut butter onto each chocolate layer. Repeat step 1 with the remaining coconut oil, protein powder and cocoa, and pour mixture on top of the half cups.<br>
    Put completed cups back into the freezer for at least 3 hours before eating.</p>
  </section>

  <footer class="page-footer">
    <span class="page-number">24</span>
    <span class="brand"><span class="brand-dot"></span>Tidewell Motion</span>
  </footer>
</main>
</body>
</html>
```